Support People to improve their image and well-being by provided personalised advise

We need a design for business cards that could be used for production on plano press. We build a new business in our region for advising mostly women (also men though) on style embracing several aspects including fashion, style, self-confidence and ultimately your internal and external image. The business card should be "classy", "french-style". The business is located in the french -speaking part of Switzerland, close to France. The name of the company is Lomu Grace

Target Market(s)

Service fees won't be cheap (medium to premium) thus we target mid-class to upper-class women (1st target) and men (2nd target)

Industry/Entity Type

Life Coaching

Contact Information for Business Card

Conseil en Image

+41 76 418 63 07
tovasel@lomu-grace.example
linkedin.example/in/sel-moran-tova

Logo Text

Lomu Grace

Colors

Designer to choose colors to be used in the design.

```html
<!DOCTYPE html>
<html lang="fr">
<head>
<meta charset="utf-8">
<title>Lomu Grace – Business Card</title>
<link rel="stylesheet" href="https://fonts.googleapis.com/css2?family=Questrial&display=swap">
<style>
  :root {
    --backdrop: #bcbcbc;
    --rose: #d96a6a;
    --rose-deep: #c95f60;
    --paper: #f4f4f4;
    --paper-shade: #e9e9e9;
    --ink: #333333;
    --ink-soft: #3c3c3c;
  }
  * { margin: 0; padding: 0; box-sizing: border-box; }
  html, body {
    width: 1200px;
    height: 576px;
    overflow: hidden;
    background: var(--backdrop);
    font-family: "Questrial", "Century Gothic", sans-serif;
  }
  .canvas {
    position: relative;
    width: 1200px;
    height: 576px;
  }
  .card {
    position: absolute;
    top: 138px;
    border-radius: 14px;
    overflow: hidden;
  }
  .card--front {
    left: 81px;
    width: 486px;
    height: 294px;
    background: linear-gradient(180deg, var(--rose) 0%, var(--rose-deep) 100%);
    display: flex;
    align-items: center;
    justify-content: center;
  }
  .card--back {
    left: 602px;
    width: 481px;
    height: 291px;
    background: linear-gradient(180deg, var(--paper) 0%, var(--paper-shade) 100%);
  }
  .wordmark {
    color: var(--ink);
    font-weight: 400;
    white-space: nowrap;
    letter-spacing: -0.5px;
  }
  .wordmark--front { font-size: 44px; }
  .wordmark--back {
    position: absolute;
    left: 46px;
    top: 54px;
    font-size: 30px;
    line-height: 1;
  }
  .holder {
    position: absolute;
    left: 47px;
    top: 137px;
  }
  .holder__name {
    color: var(--rose);
    font-size: 19px;
    line-height: 22px;
  }
  .holder__role {
    color: var(--ink-soft);
    font-size: 11.5px;
    line-height: 16px;
    margin-top: 2px;
  }
  .contact-list {
    position: absolute;
    left: 48px;
    top: 198px;
    list-style: none;
  }
  .contact-list__item {
    display: flex;
    align-items: center;
    height: 17.5px;
    color: var(--ink-soft);
    font-size: 13px;
  }
  .contact-list__icon {
    width: 11px;
    height: 11px;
    margin-right: 9px;
    fill: var(--rose);
    flex: none;
  }
</style>
</head>
<body>
<main class="canvas">
  <section class="card card--front" aria-label="Card front">
    <p class="wordmark wordmark--front">Lomu Grace</p>
  </section>

  <section class="card card--back" aria-label="Card back">
    <p class="wordmark wordmark--back">Lomu Grace</p>

    <div class="holder">
      <p class="holder__name">Ines Moreau Lenz</p>
      <p class="holder__role">Managing Director</p>
    </div>

    <ul class="contact-list">
      <li class="contact-list__item">
        <svg class="contact-list__icon" viewBox="0 0 12 12" aria-hidden="true">
          <path d="M1 3.5C1 2 2.5 1.5 6 1.5S11 2 11 3.5V5H8.5V4H3.5V5H1Z"/>
          <path d="M3 5.5H9L10.5 10.5H1.5Z"/>
        </svg>
        <span>+41 76 418 63 07</span>
      </li>
      <li class="contact-list__item">
        <svg class="contact-list__icon" viewBox="0 0 12 12" aria-hidden="true">
          <path d="M1 2.5H11V9.5H1Z M1.6 3.2L6 6.6L10.4 3.2V3H1.6Z" fill-rule="evenodd"/>
        </svg>
        <span>ines@lomu-grace.example</span>
      </li>
      <li class="contact-list__item">
        <svg class="contact-list__icon" viewBox="0 0 12 12" aria-hidden="true">
          <path d="M6 1a5 5 0 1 0 0 10A5 5 0 0 0 6 1Zm0 1.2c.7.8 1.2 2 1.3 3.2H4.7C4.8 4.2 5.3 3 6 2.2ZM2.2 6.6h1.5c.1 1.2.5 2.2 1 3A3.9 3.9 0 0 1 2.2 6.6Zm0-1.2a3.9 3.9 0 0 1 2.5-3c-.5.8-.9 1.8-1 3Zm3.8 4.4c-.7-.8-1.2-2-1.3-3.2h2.6c-.1 1.2-.6 2.4-1.3 3.2Zm1.3-.2c.5-.8.9-1.8 1-3h1.5a3.9 3.9 0 0 1-2.5 3Zm1-4.2c-.1-1.2-.5-2.2-1-3a3.9 3.9 0 0 1 2.5 3Z"/>
        </svg>
        <span>www.lomu-grace.example</span>
      </li>
    </ul>
  </section>
</main>
</body>
</html>
```